Velvet Circle club

We are looking to redesign the user interface of our mobile app “Velvet Circle”, which is the official rewards program for our luxury casino brand, Kestrane Harbour.
Our goal is to give the app a more elegant, premium, and user-friendly design that reflects the exclusivity of our brand and the luxury experience we offer our VIP clientele.
What We Need:
A complete UI design for the app’s main screens, including:
Splash Screen
01 Login / Signup Screen
02 Home Dashboard
Buttons -
Home / my card / my wallet / my booking / my host
My wallet / my offer / lucky game / my taxi / entertainment / online
03 Profile screen
04 My wallet
05 My offer
06Packages
07 My booking
08 My host
09 My card
we attached our privies app all the screen for you reference
Inspiration:
Think of luxury brands like Dunmore-Vale, Corvix Onyx, or high-end lifestyle apps. Clean interfaces, classy animations, and a sense of exclusivity are key.
We’re excited to see fresh, innovative takes that elevate the app to a truly world-class luxury experience for our users.
Thank you!
Casino

```html
<!DOCTYPE html>
<html lang="en">
<head>
<meta charset="utf-8">
<title>Velvet Circle – App Screens</title>
<link href="https://fonts.googleapis.com/css2?family=Open+Sans:wght@400;600;700&display=swap" rel="stylesheet">
<style>
:root{
  --stage:#d9d9d9;
  --ink:#1b1b1b;
  --panel:#222222;
  --gold:#f5a524;
  --gold-deep:#e39a2b;
  --white:#ffffff;
  --muted:#d8d8d8;
}
*{box-sizing:border-box;margin:0;padding:0}
html,body{width:1200px;height:824px;overflow:hidden}
body{background:var(--stage);font-family:"Open Sans",sans-serif;color:var(--white);position:relative}

.screen{position:absolute;overflow:hidden;background:
  linear-gradient(120deg,#161616 0%,#242424 22%,#141414 40%,#262626 58%,#121212 76%,#202020 100%)}
.screen--login{left:19px;top:17px;width:355px;height:769px}
.screen--home{left:425px;top:33px;width:340px;height:742px;border-radius:34px}
.screen--gaming{left:788px;top:24px;width:355px;height:768px}

.status{position:absolute;top:8px;left:26px;right:26px;display:flex;justify-content:space-between;align-items:center;font-size:13px;z-index:3}
.status__icons{display:flex;gap:5px;align-items:center}

.header{position:absolute;left:0;top:0;width:100%;background:var(--panel);border-bottom:6px solid var(--gold);border-radius:0 0 40px 40px}

/* login */
.screen--login .header{height:162px}
.brand{position:absolute;top:40px;left:0;width:100%;text-align:center}
.brand__dot{width:34px;height:34px;border-radius:50%;background:var(--gold);margin:0 auto 10px}
.brand__name{font-weight:700;font-size:24px;color:var(--gold);letter-spacing:.5px;text-transform:uppercase}

.login-card{position:absolute;left:26px;width:304px;border:1.5px solid var(--white);border-radius:8px;text-align:center}
.login-card__title{font-weight:700;font-size:16px;color:var(--gold);margin-top:20px;text-transform:uppercase}
.login-card__text{font-size:11px;line-height:18px;margin-top:10px;font-weight:600}
.btn{position:absolute;left:50%;transform:translateX(-50%);bottom:-17px;height:34px;padding:0 20px;border-radius:6px;
  background:linear-gradient(#f8b43a,#e5971f);color:var(--ink);font-size:14px;font-weight:600;letter-spacing:.6px;
  display:flex;align-items:center;justify-content:center;white-space:nowrap}
.or{position:absolute;top:559px;left:0;width:100%;text-align:center;font-weight:700;font-size:16px}
.login-foot{position:absolute;left:6px;right:6px;bottom:-20px;height:36px;background:var(--gold-deep);border-radius:28px 28px 0 0}

/* home */
.hero{position:absolute;left:0;top:0;width:100%;height:172px;border-bottom:6px solid var(--gold);border-radius:0 0 30px 30px;
  background:radial-gradient(circle at 52% 60%,#6b4418 0%,#2a1c10 28%,#0d1420 62%,#0a0f18 100%)}
.top-actions{position:absolute;display:flex;gap:10px;align-items:center;z-index:3}
.tile{position:absolute;width:128px;height:102px;border:1.5px solid var(--white);border-radius:10px 10px 32px 10px;
  background:linear-gradient(135deg,#2b2b2b 0%,#151515 45%,#2a2a2a 70%,#141414 100%);
  display:flex;flex-direction:column;align-items:center;justify-content:center;gap:10px}
.tile__label{font-weight:700;font-size:14px}
.nav{position:absolute;left:0;width:100%;background:var(--gold-deep);border-radius:30px 30px 0 0;display:flex;justify-content:space-around;padding-top:8px}
.nav__item{display:flex;flex-direction:column;align-items:center;gap:3px;color:var(--ink);font-size:9px;font-weight:600;width:58px}
.nav__icon{width:30px;height:30px;border-radius:50%;background:#1f1f1f;border:2px solid var(--white);display:flex;align-items:center;justify-content:center}
.screen--home .nav{top:675px;height:67px}

/* gaming */
.screen--gaming .header{height:137px}
.page-title{position:absolute;top:62px;left:26px;display:flex;align-items:center;gap:10px;font-weight:700;font-size:22px;color:var(--gold);letter-spacing:.5px}
.game{position:absolute;left:27px;width:302px;height:139px;border:1.5px solid var(--white);border-radius:12px 12px 34px 12px;
  background:linear-gradient(135deg,#262626,#141414 60%,#202020)}
.game__media{position:absolute;left:5px;top:6px;width:116px;height:126px;border-radius:10px}
.game__body{position:absolute;left:139px;top:14px;right:6px}
.game__title{font-size:16px;font-weight:600}
.game__text{font-size:8px;line-height:14.5px;margin-top:6px;font-weight:600}
.game__more{display:inline-block;margin-top:4px;font-size:10px;color:var(--gold);text-decoration:underline}
.screen--gaming .nav{top:710px;height:58px;padding-top:8px;border-radius:30px 30px 0 0}
</style>
</head>
<body>

<!-- Login screen -->
<section class="screen screen--login">
  <header class="header">
    <div class="status"><span>9:30</span>
      <span class="status__icons">
        <svg width="16" height="10"><rect x="0" y="7" width="3" height="3" fill="#fff"/><rect x="4" y="5" width="3" height="5" fill="#fff"/><rect x="8" y="3" width="3" height="7" fill="#fff"/><rect x="12" y="0" width="3" height="10" fill="#fff"/></svg>
        <svg width="14" height="10"><path d="M1 4a9 9 0 0 1 12 0M3.5 6.5a5.5 5.5 0 0 1 7 0" stroke="#fff" stroke-width="1.6" fill="none"/><circle cx="7" cy="9" r="1.2" fill="#fff"/></svg>
        <svg width="22" height="10"><rect x=".5" y=".5" width="19" height="9" rx="2" stroke="#fff" fill="none"/><rect x="2" y="2" width="16" height="6" rx="1" fill="#fff"/><rect x="20.5" y="3" width="1.5" height="4" fill="#fff"/></svg>
      </span>
    </div>
    <div class="brand">
      <div class="brand__dot"></div>
      <div class="brand__name">Velvet Circle</div>
    </div>
  </header>

  <div class="login-card" style="top:217px;height:132px">
    <div class="login-card__title">Member Login</div>
    <p class="login-card__text">Now you can enjoy all the excitement<br>of the casino right at your fingertips.</p>
    <div class="btn" style="width:95px">SIGN IN</div>
  </div>

  <div class="login-card" style="top:389px;height:131px">
    <div class="login-card__title">New Member Login</div>
    <p class="login-card__text">If you are a first time user, please go<br>through the sign up process</p>
    <div class="btn" style="width:95px">SIGN UP</div>
  </div>

  <div class="or">Or</div>

  <div class="login-card" style="top:601px;height:106px">
    <p class="login-card__text" style="margin-top:26px">If you are with a temporary ID, sign in<br>here</p>
    <div class="btn" style="width:166px">TEMPORARY SIGNIN</div>
  </div>

  <div class="login-foot"></div>
</section>

<!-- Home dashboard -->
<section class="screen screen--home">
  <div class="hero" role="img" aria-label="Glowing playing cards, dice and roulette wheel on a dark background"></div>
  <div class="status" style="left:26px;right:34px"><span>9:30</span>
    <span class="status__icons">
      <svg width="14" height="10"><path d="M1 4a9 9 0 0 1 12 0M3.5 6.5a5.5 5.5 0 0 1 7 0" stroke="#fff" stroke-width="1.6" fill="none"/><circle cx="7" cy="9" r="1.2" fill="#fff"/></svg>
      <svg width="22" height="10"><rect x=".5" y=".5" width="19" height="9" rx="2" stroke="#fff" fill="none"/><rect x="2" y="2" width="16" height="6" rx="1" fill="#fff"/></svg>
    </span>
  </div>
  <div class="top-actions" style="top:46px;right:28px">
    <svg width="14" height="12"><path d="M0 1h14M0 6h14M0 11h14" stroke="#f5a524" stroke-width="2"/></svg>
    <svg width="14" height="14"><path d="M7 1a4 4 0 0 0-4 4v4L1 11h12l-2-2V5a4 4 0 0 0-4-4z" fill="#f5a524"/><circle cx="7" cy="12.5" r="1.5" fill="#f5a524"/></svg>
  </div>

  <div class="tile" style="left:26px;top:229px">
    <svg width="36" height="30" viewBox="0 0 36 30"><path d="M6 9l18-7 3 7z" fill="#f5a524"/><rect x="2" y="9" width="32" height="20" rx="3" fill="#f5a524"/><rect x="22" y="15" width="12" height="8" rx="2" fill="#1b1b1b"/><circle cx="26" cy="19" r="1.6" fill="#f5a524"/></svg>
    <span class="tile__label">My Wallet</span></div>
  <div class="tile" style="left:185px;top:229px">
    <svg width="38" height="38" viewBox="0 0 38 38"><path d="M19 1l5 4 6-1 2 6 5 3-2 6 2 6-5 3-2 6-6-1-5 4-5-4-6 1-2-6-5-3 2-6-2-6 5-3 2-6 6 1z" fill="#f5a524"/><circle cx="14" cy="14" r="3" fill="#1b1b1b"/><circle cx="24" cy="24" r="3" fill="#1b1b1b"/><path d="M25 12L13 26" stroke="#1b1b1b" stroke-width="3"/></svg>
    <span class="tile__label">My Offer</span></div>
  <div class="tile" style="left:26px;top:362px">
    <svg width="38" height="38" viewBox="0 0 38 38"><rect x="2" y="2" width="20" height="20" rx="4" fill="#f5a524"/><rect x="16" y="16" width="20" height="20" rx="4" fill="#f5a524" stroke="#1b1b1b" stroke-width="2"/><circle cx="8" cy="8" r="2" fill="#1b1b1b"/><circle cx="16" cy="16" r="2" fill="#1b1b1b" opacity="0"/><circle cx="22" cy="22" r="2" fill="#1b1b1b"/><circle cx="30" cy="30" r="2" fill="#1b1b1b"/></svg>
    <span class="tile__label">Lucky Game</span></div>
  <div class="tile" style="left:185px;top:362px">
    <svg width="40" height="34" viewBox="0 0 40 34"><rect x="14" y="1" width="12" height="5" rx="1" fill="#f5a524"/><path d="M8 8h24l5 11v11H3V19z" fill="#f5a524"/><path d="M11 11h18l3 7H8z" fill="#1b1b1b"/><circle cx="10" cy="23" r="3" fill="#1b1b1b"/><circle cx="30" cy="23" r="3" fill="#1b1b1b"/><rect x="5" y="30" width="6" height="4" fill="#f5a524"/><rect x="29" y="30" width="6" height="4" fill="#f5a524"/></svg>
    <span class="tile__label">My Taxi</span></div>
  <div class="tile" style="left:26px;top:503px">
    <svg width="38" height="38" viewBox="0 0 38 38"><rect x="2" y="2" width="15" height="15" rx="3" fill="#f5a524"/><rect x="21" y="2" width="15" height="15" rx="3" fill="#f5a524"/><rect x="2" y="21" width="15" height="15" rx="3" fill="#f5a524"/><rect x="21" y="21" width="15" height="15" rx="3" fill="#f5a524"/><path d="M26 25l6 3.5-6 3.5z" fill="#1b1b1b"/><path d="M25 9h7M25 12h5" stroke="#1b1b1b" stroke-width="2"/></svg>
    <span class="tile__label">Entertainment</span></div>
  <div class="tile" style="left:185px;top:503px">
    <svg width="40" height="38" viewBox="0 0 40 38"><rect x="3" y="6" width="30" height="22" rx="2" fill="none" stroke="#f5a524" stroke-width="3"/><rect x="22" y="1" width="16" height="11" rx="3" fill="#f5a524"/><circle cx="18" cy="15" r="4" fill="#f5a524"/><path d="M10 28a8 8 0 0 1 16 0z" fill="#f5a524"/><rect x="1" y="32" width="34" height="3" fill="#f5a524"/></svg>
    <span class="tile__label">Online</span></div>

  <nav class="nav">
    <div class="nav__item"><span class="nav__icon"><svg width="16" height="14"><path d="M8 1L1 7h2v6h4V9h2v4h4V7h2z" fill="#f5a524"/></svg></span>Home</div>
    <div class="nav__item"><span class="nav__icon"><svg width="14" height="14"><circle cx="7" cy="4" r="3" fill="#fff"/><path d="M1 14a6 6 0 0 1 12 0z" fill="#fff"/></svg></span>My Card</div>
    <div class="nav__item"><span class="nav__icon"><svg width="14" height="12"><rect x="0" y="1" width="14" height="11" rx="2" fill="#fff"/><rect x="8" y="5" width="6" height="4" fill="#1f1f1f"/></svg></span>My Wallet</div>
    <div class="nav__item"><span class="nav__icon"><svg width="14" height="14"><rect x="0" y="2" width="14" height="12" rx="2" fill="#fff"/><path d="M2 6h10M2 9h10M5 5v8M9 5v8" stroke="#1f1f1f"/></svg></span>My Booking</div>
    <div class="nav__item"><span class="nav__icon"><svg width="12" height="14"><rect x="0" y="0" width="12" height="14" rx="2" fill="#fff"/><circle cx="6" cy="5" r="2" fill="#1f1f1f"/><path d="M2 11a4 4 0 0 1 8 0z" fill="#1f1f1f"/></svg></span>My Host</div>
  </nav>
</section>

<!-- Gaming screen -->
<section class="screen screen--gaming">
  <header class="header">
    <div class="status"><span>9:30</span>
      <span class="status__icons">
        <svg width="16" height="10"><rect x="0" y="7" width="3" height="3" fill="#fff"/><rect x="4" y="5" width="3" height="5" fill="#fff"/><rect x="8" y="3" width="3" height="7" fill="#fff"/><rect x="12" y="0" width="3" height="10" fill="#fff"/></svg>
        <svg width="14" height="10"><path d="M1 4a9 9 0 0 1 12 0M3.5 6.5a5.5 5.5 0 0 1 7 0" stroke="#fff" stroke-width="1.6" fill="none"/><circle cx="7" cy="9" r="1.2" fill="#fff"/></svg>
        <svg width="22" height="10"><rect x=".5" y=".5" width="19" height="9" rx="2" stroke="#fff" fill="none"/><rect x="2" y="2" width="16" height="6" rx="1" fill="#fff"/></svg>
      </span>
    </div>
    <div class="page-title">
      <svg width="12" height="20"><path d="M10 2L3 10l7 8" stroke="#f5a524" stroke-width="3" fill="none"/></svg>GAMING
    </div>
    <div class="top-actions" style="top:71px;right:30px">
      <svg width="14" height="12"><path d="M0 1h14M0 6h14M0 11h14" stroke="#f5a524" stroke-width="2"/></svg>
      <svg width="14" height="14"><path d="M7 1a4 4 0 0 0-4 4v4L1 11h12l-2-2V5a4 4 0 0 0-4-4z" fill="#f5a524"/><circle cx="7" cy="12.5" r="1.5" fill="#f5a524"/></svg>
    </div>
  </header>

  <article class="game" style="top:177px">
    <div class="game__media" role="img" aria-label="Neon-lit playing cards fanned beside casino chips" style="background:radial-gradient(circle at 55% 55%,#c24a14,#4a1a10 55%,#1a1418)"></div>
    <div class="game__body">
      <h2 class="game__title">Baccarat</h2>
      <p class="game__text">A timeless card game and one of the most popular tables on our floor. Kestrane Harbour offers baccarat tables for all players, both high stakes and low limits.</p>
      <span class="game__more">View More</span>
    </div>
  </article>

  <article class="game" style="top:344px">
    <div class="game__media" role="img" aria-label="Golden roulette wheel with scattered chips" style="background:radial-gradient(circle at 50% 55%,#8a6a2e,#3a2c18 50%,#1c1812)"></div>
    <div class="game__body">
      <h2 class="game__title">Roulette</h2>
      <p class="game__text">A classic casino game where players bet on which red or black numbered pocket of a spinning wheel the ball will come to rest in when the wheel stops.</p>
      <span class="game__more">View More</span>
    </div>
  </article>

  <article class="game" style="top:507px">
    <div class="game__media" role="img" aria-label="Dark blue casino chip with gold accents" style="background:radial-gradient(circle at 45% 50%,#4a6488,#1c2a40 55%,#0e1420)"></div>
    <div class="game__body">
      <h2 class="game__title">Blackjack</h2>
      <p class="game__text">Blackjack is a card game where players aim for a hand total higher than the dealer's cards, up to but not exceeding 21.</p>
      <span class="game__more">View More</span>
    </div>
  </article>

  <article class="game" style="top:673px">
    <div class="game__media" role="img" aria-label="Blackjack table artwork" style="background:linear-gradient(#2a4060,#14202e)"></div>
    <div class="game__body">
      <h2 class="game__title">Blackjack</h2>
    </div>
  </article>

  <nav class="nav">
    <div class="nav__item"><span class="nav__icon"><svg width="16" height="14"><path d="M8 1L1 7h2v6h4V9h2v4h4V7h2z" fill="#fff"/></svg></span>Home</div>
    <div class="nav__item"><span class="nav__icon"><svg width="14" height="14"><circle cx="7" cy="4" r="3" fill="#fff"/><path d="M1 14a6 6 0 0 1 12 0z" fill="#fff"/></svg></span>My Card</div>
    <div class="nav__item"><span class="nav__icon"><svg width="14" height="12"><rect x="0" y="1" width="14" height="11" rx="2" fill="#fff"/><rect x="8" y="5" width="6" height="4" fill="#1f1f1f"/></svg></span>My Wallet</div>
    <div class="nav__item"><span class="nav__icon"><svg width="14" height="14"><rect x="0" y="2" width="14" height="12" rx="2" fill="#fff"/><path d="M2 6h10M2 9h10M5 5v8M9 5v8" stroke="#1f1f1f"/></svg></span>My Booking</div>
    <div class="nav__item"><span class="nav__icon"><svg width="12" height="14"><rect x="0" y="0" width="12" height="14" rx="2" fill="#fff"/><circle cx="6" cy="5" r="2" fill="#1f1f1f"/><path d="M2 11a4 4 0 0 1 8 0z" fill="#1f1f1f"/></svg></span>My Host</div>
  </nav>
</section>

</body>
</html>
```